Business Card Design Project

We are a construction company in Orange County, CA. We need a two sided business card. We would like the back to be our logo with web URL. Front should included Name, title, address, phone, fax and email address.

our address is
627 West Dorrance Blvd, Suite 308
Anaheim, CA 92718

Our logo files are attached.

Construction

```html
<!DOCTYPE html>
<html lang="en">
<head>
<meta charset="utf-8">
<title>Keston Business Card</title>
<link href="https://fonts.googleapis.com/css2?family=Open+Sans:ital,wght@0,400;0,600;0,700;0,800;1,700&display=swap" rel="stylesheet">
<style>
  :root {
    --brand-blue: #124a7e;
    --band-grey: #a7a9ac;
    --ink: #333333;
    --paper: #ffffff;
    --backdrop: #d9d9d9;
  }
  * { margin: 0; padding: 0; box-sizing: border-box; }
  html, body { width: 960px; height: 1200px; overflow: hidden; }
  body {
    background: var(--backdrop);
    font-family: "Open Sans", Arial, sans-serif;
    position: relative;
  }
  .card {
    position: absolute;
    background: var(--paper);
    border-radius: 30px;
    overflow: hidden;
  }
  .card--front { left: 70px; top: 107px; width: 838px; height: 478px; }
  .card--back { left: 60px; top: 645px; width: 840px; height: 477px; }

  .wordmark {
    position: absolute;
    left: 0; width: 100%;
    text-align: center;
    color: var(--brand-blue);
    font-weight: 800;
    line-height: 1;
    white-space: nowrap;
  }
  .card--front .wordmark { top: 73px; font-size: 124px; letter-spacing: -2px; }
  .card--back .wordmark { top: 151px; font-size: 168px; letter-spacing: -3px; }

  .info-bands { position: absolute; left: 0; top: 269px; width: 838px; height: 104px; }
  .holder { position: absolute; left: 38px; top: 292px; color: var(--paper); }
  .holder__name { font-size: 24px; font-weight: 600; line-height: 32px; }
  .holder__title { font-size: 19px; font-weight: 600; line-height: 26px; }

  .contact {
    position: absolute; right: 40px; top: 290px;
    color: var(--paper); font-size: 19px; text-align: right; line-height: 38px;
    white-space: nowrap;
  }
  .contact b { font-weight: 700; font-style: italic; }
  .contact .sep { margin: 0 6px; }

  .address {
    position: absolute; left: 0; width: 100%; top: 421px;
    text-align: center; color: var(--ink); font-size: 24px;
    white-space: nowrap;
  }
  .web {
    position: absolute; left: 0; width: 100%; top: 398px;
    text-align: center; color: var(--ink); font-size: 28px; font-weight: 700;
  }
</style>
</head>
<body>
  <section class="card card--front">
    <div class="wordmark">KESTON</div>

    <svg class="info-bands" viewBox="0 0 838 104" aria-hidden="true">
      <polygon points="0,0 385,0 283,104 0,104" fill="var(--brand-blue)"/>
      <polygon points="400,0 838,0 838,104 302,104" fill="var(--band-grey)"/>
    </svg>

    <div class="holder">
      <div class="holder__name">Your Name</div>
      <div class="holder__title">Designation</div>
    </div>

    <div class="contact">
      <div><b>p</b> : 1-234-4567 <span class="sep">|</span> <b>f</b> : 1-234-4567</div>
      <div><b>e</b> : info@keston.com <span class="sep">|</span> <b>w</b> : www.keston.com</div>
    </div>

    <div class="address">627 West Dorrance Blvd, Suite 308, Anaheim, CA 92718</div>
  </section>

  <section class="card card--back">
    <div class="wordmark">KESTON</div>
    <div class="web">www.keston.com</div>
  </section>
</body>
</html>
```